Quorva - corporate Business Card

We need a good look and innovative business card for a new start up company based in Los Angeles called "Quorva". We are in a payment business, including payment card, app, and ewallet. We are expert in online payment and Card not present (CNP) transaction.
We need an innovative, modern business card.

Our logo font is Aero Matics

Target Market(s)

Startup - Bank - Online Payment - Card Manufacturing

Industry/Entity Type

Startup

Contact Information for Business Card

phone: 555 014 7396 - Address: 4172 Marlowe blvd, Brenton Park, CA 90299

Requirements
Must have
• Message: innovative, professional, expert, high tech, trust, online payment expert, security
Nice to have
• no comment
Should not have
• no Comment

```html
<!DOCTYPE html>
<html lang="en">
<head>
<meta charset="utf-8">
<title>Quorva – Business Card</title>
<link rel="stylesheet" href="https://fonts.googleapis.com/css2?family=Open+Sans:wght@400;600;700&display=swap">
<style>
  :root {
    --brand-red: #b81e2e;
    --card-dark: #2a2a2a;
    --card-white: #ffffff;
    --ink: #3a3a3a;
    --backdrop: #e9e6e2;
  }
  * { box-sizing: border-box; margin: 0; padding: 0; }
  html, body { width: 1200px; height: 900px; overflow: hidden; }
  body {
    background: var(--backdrop);
    font-family: "Open Sans", Arial, sans-serif;
    position: relative;
  }
  .card {
    position: absolute;
    left: 320px;
    width: 560px;
    height: 320px;
    overflow: hidden;
    box-shadow: 0 6px 18px rgba(0,0,0,0.18);
  }
  .card--back { top: 70px; background: var(--card-dark); }
  .card--front { top: 480px; background: var(--card-white); }

  .brand {
    position: absolute;
    display: flex;
    align-items: center;
    gap: 14px;
  }
  .brand__dot { width: 78px; height: 78px; border-radius: 50%; flex: none; }
  .brand__name { font-weight: 600; font-size: 64px; letter-spacing: 4px; line-height: 1; }

  .card--back .brand { left: 70px; top: 121px; }
  .card--back .brand__dot { background: var(--card-white); }
  .card--back .brand__name { color: var(--card-white); }

  .card--front .brand { left: 226px; top: 118px; }
  .card--front .brand__dot { background: var(--brand-red); width: 70px; height: 70px; }
  .card--front .brand__name { color: var(--brand-red); font-size: 58px; }

  .corner-mark { position: absolute; left: 0; top: 0; }
  .holder { position: absolute; left: 66px; top: 16px; }
  .holder__name { color: var(--brand-red); font-weight: 700; font-size: 18px; line-height: 1.15; }
  .holder__role { color: var(--ink); font-size: 13px; }

  .contact { position: absolute; left: 24px; top: 124px; color: var(--ink); font-size: 14px; line-height: 1.45; }
  .contact__row { display: flex; align-items: center; gap: 7px; }
  .contact__icon { width: 11px; height: 11px; flex: none; }
  .contact__address { margin-top: 10px; }

  .footer-band { position: absolute; left: 0; bottom: 0; }
</style>
</head>
<body>
  <section class="card card--back" aria-label="Business card back">
    <div class="brand">
      <span class="brand__dot"></span>
      <span class="brand__name">quorva</span>
    </div>
  </section>

  <section class="card card--front" aria-label="Business card front">
    <svg class="corner-mark" width="60" height="44" viewBox="0 0 60 44" aria-hidden="true">
      <polygon points="0,0 28,0 0,36" fill="var(--brand-red)"/>
      <polygon points="34,0 56,0 56,44 6,44" fill="var(--brand-red)"/>
    </svg>
    <div class="holder">
      <div class="holder__name">Daniel Reyes</div>
      <div class="holder__role">Managing Director</div>
    </div>

    <div class="brand">
      <span class="brand__dot"></span>
      <span class="brand__name">quorva</span>
    </div>

    <div class="contact">
      <div class="contact__row">
        <svg class="contact__icon" viewBox="0 0 10 10" aria-hidden="true">
          <path d="M2 0.5 L3.6 0.5 L4.2 3 L3 3.8 Q4 6 6.2 7 L7 5.8 L9.5 6.4 L9.5 8 Q9.5 9.5 8 9.5 Q1 9 0.5 2 Q0.5 0.5 2 0.5 Z" fill="var(--brand-red)"/>
        </svg>
        <span>555 014 7396</span>
      </div>
      <div class="contact__row">
        <svg class="contact__icon" viewBox="0 0 10 10" aria-hidden="true">
          <circle cx="5" cy="5" r="4.5" fill="var(--brand-red)"/>
          <path d="M0.5 5 H9.5 M5 0.5 Q2.5 5 5 9.5 M5 0.5 Q7.5 5 5 9.5" stroke="#fff" stroke-width="0.8" fill="none"/>
        </svg>
        <span>www.quorva.com</span>
      </div>
      <div class="contact__address">4172 Marlowe blvd,<br>Brenton Park, CA 90299</div>
    </div>

    <svg class="footer-band" width="560" height="36" viewBox="0 0 560 36" aria-hidden="true">
      <polygon points="0,6 176,6 168,36 0,36" fill="var(--brand-red)"/>
      <polygon points="184,6 560,6 560,36 176,36" fill="var(--brand-red)"/>
    </svg>
  </section>
</body>
</html>
```